IT Services Company Needs Corporate PPT Template

This is urgent (need a fast turn around). We need a corporate PPT template deck (NOTE: Deck should be in 4:3 ratio) for our IT Services firm that is clean but slick and modern. We tend to lean more towards the flat design look. I'm attaching a zip file which includes our Corporate Branding Guide (which is in progress), color scheme, A PPT deck as inspiration (our logo is on the last slide), our font (LATO). Our newly launched website is located at: http://www.veranthix.com.

As an example of a deck we like see: http://slidemorrow.net/item/clean-multipurpose-business-presentation-template/5318206?WT.ac=category_thumb&WT.seg_1=category_thumb&WT.z_author=PixelHarbor
Although we don't want "this" deck - it gives an idea of style.

I'm also attaching a copy of our corporate deck as it is now to give you an idea of the type of content that would appear on various slides. We definitely want the following slides (at least) within the template:

Title Slide
Blank Slide
2 Column - with bullets
2 Column - no bullets
Single Column - no bullets
Single Column - with bullets
Various Charts and Tables (see example deck)
Meet the Team
Offering Slide
Customer Showcase
Timeline
Case Study
Contact US

Note: Being awarded this job will lead to a second job of creating our corporate deck.

Target Market(s)

CIO, CEO, Technology Officers, Sales People, Marketing, IT heads and staff, Customers, Prospective customers

Industry/Entity Type

Business

Requirements
Must have
• See description and attached files

```html
<!DOCTYPE html>
<html lang="en">
<head>
<meta charset="utf-8">
<title>Project Title Here</title>
<link rel="stylesheet" href="https://fonts.googleapis.com/css2?family=Lato:wght@400;700;900&display=swap">
<style>
  :root {
    --header-dark: #035a80;
    --header-mid: #066a94;
    --title-tint: #a9d9ef;
    --accent: #3a97e0;
    --card-border: #4a9fe2;
    --body-text: #2e2e2e;
    --footer: #0a7fae;
    --footer-dark: #06709c;
    --white: #ffffff;
    --page: #ffffff;
    --page-shade: #efefef;
  }
  * { box-sizing: border-box; margin: 0; padding: 0; }
  html, body { width: 1200px; height: 900px; overflow: hidden; }
  body { font-family: "Lato", Arial, sans-serif; background: var(--page); }
  .slide {
    position: relative; width: 1200px; height: 900px; overflow: hidden;
    background: linear-gradient(to bottom, var(--page-shade) 0, var(--page) 150px, var(--page) 720px, var(--page-shade) 840px);
  }
  .slide-header {
    position: absolute; left: 0; top: 0; width: 1200px; height: 87px;
    background: linear-gradient(to bottom, var(--header-mid), var(--header-dark));
  }
  .slide-header .pointer {
    position: absolute; left: 52px; top: 87px; width: 0; height: 0;
    border-left: 23px solid transparent; border-right: 23px solid transparent;
    border-top: 21px solid var(--header-dark);
  }
  .slide-title {
    position: absolute; left: 28px; top: 18px;
    font-size: 39px; font-weight: 700; color: var(--title-tint); letter-spacing: 0.2px;
  }
  .feature {
    position: absolute; width: 462px; height: 120px;
  }
  .feature-box {
    position: absolute; left: 107px; top: 0; width: 355px; height: 120px;
    border: 1.5px solid var(--card-border); background: var(--white);
  }
  .feature-hex { position: absolute; left: 0; top: 0; width: 140px; height: 120px; }
  .feature-text {
    position: absolute; left: 159px; top: 15px; width: 273px;
    font-size: 16.5px; line-height: 24px; color: var(--body-text);
    text-align: justify;
  }
  .col-left { left: 93px; }
  .col-right { left: 620px; }
  .row-1 { top: 240px; }
  .row-2 { top: 406px; }
  .row-3 { top: 588px; }
  .slide-footer {
    position: absolute; left: 0; bottom: 0; width: 1200px; height: 60px;
    background: linear-gradient(to bottom, var(--footer), var(--footer-dark));
  }
  .brand {
    position: absolute; left: 20px; top: 10px;
    font-size: 32px; font-weight: 900; color: var(--white); letter-spacing: 0.5px;
  }
  .connect {
    position: absolute; left: 819px; top: 22px;
    font-size: 15px; font-weight: 400; color: var(--white); letter-spacing: 0.2px;
  }
  .social {
    position: absolute; left: 974px; top: 13px; display: flex; align-items: center;
  }
  .social-item {
    width: 30px; height: 30px; background: rgba(255,255,255,0.92); border-radius: 3px;
  }
  .social-divider { width: 2px; height: 32px; background: var(--white); margin: 0 6px; }
</style>
</head>
<body>
<div class="slide">
  <header class="slide-header">
    <h1 class="slide-title">Project Title Here</h1>
    <span class="pointer"></span>
  </header>

  <!-- Feature: conversation -->
  <section class="feature col-left row-1">
    <div class="feature-box"></div>
    <svg class="feature-hex" viewBox="0 0 140 120">
      <polygon points="0,60 35,0 107,0 140,60 107,120 35,120" fill="var(--accent)"/>
      <g fill="none" stroke="#fff" stroke-width="2" stroke-linejoin="round">
        <path d="M58 38 h37 a4 4 0 0 1 4 4 v20 a4 4 0 0 1 -4 4 h-3 l4 9 l-12 -9 h-26 a4 4 0 0 1 -4 -4 v-20 a4 4 0 0 1 4 -4z"/>
        <path d="M44 46 h35 a4 4 0 0 1 4 4 v20 a4 4 0 0 1 -4 4 h-24 l-11 9 l3 -9 h-3 a4 4 0 0 1 -4 -4 v-20 a4 4 0 0 1 4 -4z" fill="var(--accent)"/>
      </g>
    </svg>
    <p class="feature-text">Lorem ipsum dolor sit Lorem ipsum dolor sit Lorem ipsum dolor sit Lorem ipsum dolor sit Lorem ipsum dolor sit Lorem ipsum dolor</p>
  </section>

  <!-- Feature: download to cart -->
  <section class="feature col-right row-1">
    <div class="feature-box"></div>
    <svg class="feature-hex" viewBox="0 0 140 120">
      <polygon points="0,60 35,0 107,0 140,60 107,120 35,120" fill="var(--accent)"/>
      <g fill="none" stroke="#fff" stroke-width="2" stroke-linecap="round" stroke-linejoin="round">
        <path d="M42 44 h7 l6 26 h30 l6 -20"/>
        <line x1="70" y1="36" x2="70" y2="58"/>
        <polyline points="63,51 70,58 77,51"/>
        <circle cx="59" cy="78" r="3.5"/>
        <circle cx="82" cy="78" r="3.5"/>
      </g>
    </svg>
    <p class="feature-text">Lorem ipsum dolor sit Lorem ipsum dolor sit Lorem ipsum dolor sit Lorem ipsum dolor sit Lorem ipsum dolor sit Lorem ipsum dolor</p>
  </section>

  <!-- Feature: cart -->
  <section class="feature col-left row-2">
    <div class="feature-box"></div>
    <svg class="feature-hex" viewBox="0 0 140 120">
      <polygon points="0,60 35,0 107,0 140,60 107,120 35,120" fill="var(--accent)"/>
      <g fill="none" stroke="#fff" stroke-width="2" stroke-linecap="round" stroke-linejoin="round">
        <path d="M40 40 h8 l7 27 h30 l7 -19 h-40"/>
        <circle cx="58" cy="77" r="3.5"/>
        <circle cx="82" cy="77" r="3.5"/>
      </g>
    </svg>
    <p class="feature-text">Lorem ipsum dolor sit Lorem ipsum dolor sit Lorem ipsum dolor sit Lorem ipsum dolor sit Lorem ipsum dolor sit Lorem ipsum dolor</p>
  </section>

  <!-- Feature: settings -->
  <section class="feature col-right row-2">
    <div class="feature-box"></div>
    <svg class="feature-hex" viewBox="0 0 140 120">
      <polygon points="0,60 35,0 107,0 140,60 107,120 35,120" fill="var(--accent)"/>
      <g fill="none" stroke="#fff" stroke-width="2" stroke-linejoin="round">
        <path d="M66 39 h8 l1.5 6 l5 2.2 l5.3 -3.2 l5.6 5.6 l-3.2 5.3 l2.2 5 l6 1.5 v8 l-6 1.5 l-2.2 5 l3.2 5.3 l-5.6 5.6 l-5.3 -3.2 l-5 2.2 l-1.5 6 h-8 l-1.5 -6 l-5 -2.2 l-5.3 3.2 l-5.6 -5.6 l3.2 -5.3 l-2.2 -5 l-6 -1.5 v-8 l6 -1.5 l2.2 -5 l-3.2 -5.3 l5.6 -5.6 l5.3 3.2 l5 -2.2z"/>
        <circle cx="70" cy="61" r="8"/>
      </g>
    </svg>
    <p class="feature-text">Lorem ipsum dolor sit Lorem ipsum dolor sit Lorem ipsum dolor sit Lorem ipsum dolor sit Lorem ipsum dolor sit Lorem ipsum dolor</p>
  </section>

  <!-- Feature: folder -->
  <section class="feature col-left row-3">
    <div class="feature-box"></div>
    <svg class="feature-hex" viewBox="0 0 140 120">
      <polygon points="0,60 35,0 107,0 140,60 107,120 35,120" fill="var(--accent)"/>
      <g fill="none" stroke="#fff" stroke-width="2" stroke-linejoin="round">
        <path d="M44 44 h17 l4 5 h31 v29 h-52z"/>
        <line x1="44" y1="53" x2="96" y2="53"/>
      </g>
    </svg>
    <p class="feature-text">Lorem ipsum dolor sit Lorem ipsum dolor sit Lorem ipsum dolor sit Lorem ipsum dolor sit Lorem ipsum dolor sit Lorem ipsum dolor</p>
  </section>

  <!-- Feature: folder -->
  <section class="feature col-right row-3">
    <div class="feature-box"></div>
    <svg class="feature-hex" viewBox="0 0 140 120">
      <polygon points="0,60 35,0 107,0 140,60 107,120 35,120" fill="var(--accent)"/>
      <g fill="none" stroke="#fff" stroke-width="2" stroke-linejoin="round">
        <path d="M44 44 h17 l4 5 h31 v29 h-52z"/>
        <line x1="44" y1="53" x2="96" y2="53"/>
      </g>
    </svg>
    <p class="feature-text">Lorem ipsum dolor sit Lorem ipsum dolor sit Lorem ipsum dolor sit Lorem ipsum dolor sit Lorem ipsum dolor sit Lorem ipsum dolor</p>
  </section>

  <footer class="slide-footer">
    <div class="brand">Veranthix</div>
    <div class="connect">CONNECT WITH US:</div>
    <div class="social" aria-label="Social channels">
      <span class="social-item"></span>
      <span class="social-divider"></span>
      <span class="social-item"></span>
      <span class="social-divider"></span>
      <span class="social-item"></span>
      <span class="social-divider"></span>
      <span class="social-item"></span>
      <span class="social-divider"></span>
      <span class="social-item"></span>
    </div>
  </footer>
</div>
</body>
</html>
```